CONTACT US Page and design for website

We need a contact us page for our website. We would like it to have a message area, a map, our information, etc.

Please see the text attachment for what we are looking for. We need to have something that is creative and interesting, modern and professional.

We believe that a contact US page should be very creative because everyone clicks that to contact us. We want it to be super professional, attention grabbing, pleasing to the eye.

PLEASE KEEP THE HEADER AND FOOTER THE SAME, ONLY THE ACTUAL CONTACT US PAGE NEEDS TO BE WORKED ON. THANKS!
We are excited to work with designers for this project.

Target Market(s)

Clients in technology business

Industry/Entity Type

Information Technology

Number of Pages Required

1 page

Font styles to use
Serif

Requirements
Must have
• CHECK THE TEXT ATTACHMENT PLEASE
• Must stay within our design colors and theme.
Nice to have
• see attachment
Should not have
• it should be special

```html
<!DOCTYPE html>
<html lang="en">
<head>
<meta charset="utf-8">
<title>Contact Us – Nexora Tech</title>
<link href="https://fonts.googleapis.com/css2?family=Open+Sans:wght@400;600;700&display=swap" rel="stylesheet">
<style>
:root{
  --teal:#35c1b4;
  --teal-dark:#2aa89c;
  --slate:#3d5b5e;
  --ink:#333;
  --muted:#777;
  --line:#e2e2e2;
  --footer:#c4c4c4;
  --footer-dark:#a3a3a3;
  --white:#fff;
}
*{box-sizing:border-box;margin:0;padding:0}
html,body{width:716px;height:1200px;overflow:hidden}
body{font-family:"Open Sans",sans-serif;color:var(--ink);background:var(--white);position:relative;font-size:9px}
.site-header{height:67px;border-bottom:1px solid var(--line);position:relative}
.brand{position:absolute;left:70px;top:10px;display:flex;align-items:center;gap:7px}
.brand-mark{width:20px;height:20px;background:var(--teal)}
.brand-name{font-weight:700;font-size:17px;color:var(--teal);letter-spacing:1px;line-height:1}
.brand-tag{font-size:6px;color:var(--teal);letter-spacing:1.5px;text-transform:uppercase;margin-top:2px}
.header-tools{position:absolute;right:70px;top:13px;display:flex;align-items:center;gap:12px;font-size:8px;color:var(--muted)}
.header-phone{display:flex;align-items:center;gap:5px;font-weight:700;font-size:12px;color:var(--ink)}
.main-nav{position:absolute;left:70px;right:70px;top:48px;display:flex;align-items:center;gap:14px;font-size:6.5px;text-transform:uppercase;color:#555;letter-spacing:.4px}
.search{margin-left:auto;width:60px;height:13px;border:1px solid #ccc;font-size:6.5px;padding:2px 4px;color:#999}
.cart-box{width:15px;height:13px;border:1px solid #ccc}
.hero{height:196px;background:linear-gradient(120deg,#cfd4d6 0%,#eef0f1 45%,#b9bec1 100%)}
.page-title{font-size:20px;font-weight:400;color:#444;margin:22px 0 0 84px}
.location{position:absolute;left:84px;top:317px;width:553px;height:173px;display:flex;border:1px solid var(--line)}
.office-panel{width:163px;background:var(--slate);color:var(--white);padding:60px 0 0 14px}
.office-panel h3{font-size:8px;font-weight:600;text-transform:uppercase;letter-spacing:.4px;margin-bottom:4px}
.office-panel p{font-size:7px;line-height:1.35;opacity:.9}
.map{flex:1;background:linear-gradient(135deg,#eceae4,#f6f4ef 50%,#e4e1da)}
.message-center{position:absolute;left:0;top:513px;width:716px;height:203px;background:var(--teal);padding:30px 0 0 96px}
.message-center h2{color:var(--white);font-size:11px;font-weight:600;text-transform:uppercase;letter-spacing:.3px}
.form{display:flex;gap:12px;margin-top:14px}
.fields{width:250px;display:flex;flex-direction:column;gap:10px}
.field{height:22px;background:var(--white);border:1px solid #d8d8d8;font-size:7px;color:#999;padding:6px 6px}
.message{width:270px;height:82px;background:var(--white);border:1px solid #d8d8d8;font-size:7px;color:#999;padding:6px}
.submit{margin-top:11px;width:95px;height:22px;background:#111;color:var(--white);font-size:8px;font-weight:700;text-transform:uppercase;padding:6px 0 0 14px}
.info{position:absolute;top:742px;left:84px;right:70px;display:flex}
.info h4{font-size:10px;font-weight:700;text-transform:uppercase;margin-bottom:12px}
.hours{width:326px}
.hours li{list-style:none;font-size:7.5px;color:#555;line-height:2.15}
.hours .note{font-size:7px;color:#777;margin-top:4px}
.social-title{margin-top:28px}
.social{display:flex;gap:4px}
.social span{width:14px;height:14px;background:var(--teal-dark)}
.contact-info{flex:1}
.contact-grid{display:grid;grid-template-columns:1fr 1fr;row-gap:18px}
.contact-grid h5{font-size:7px;font-weight:600;margin-bottom:4px}
.contact-grid p{font-size:7px;color:#555;display:flex;align-items:center;gap:5px;line-height:2}
.site-footer{position:absolute;left:0;top:974px;width:716px;height:226px;background:var(--footer);color:#555}
.footer-about{width:480px;margin:10px auto 0;text-align:center;font-size:6.5px;line-height:1.45}
.footer-contact{display:flex;justify-content:center;gap:40px;margin-top:14px;font-size:6.5px}
.footer-contact span{display:flex;align-items:center;gap:4px}
.footer-links{display:flex;justify-content:center;gap:34px;margin-top:14px;font-size:7px;font-weight:600}
.footer-bottom{position:absolute;left:0;bottom:0;width:716px;height:98px;background:var(--footer-dark);text-align:center;color:#444}
.footer-social{display:flex;justify-content:center;gap:10px;margin-top:36px}
.footer-social span{width:13px;height:13px;border:1px solid #666;border-radius:50%}
.copyright{font-size:6.5px;margin-top:12px;line-height:1.4}
</style>
</head>
<body>
<header class="site-header">
  <div class="brand">
    <span class="brand-mark"></span>
    <div><div class="brand-name">NEXORA TECH</div><div class="brand-tag">Engineering what's next</div></div>
  </div>
  <div class="header-tools">
    <span>LIVE CHAT</span>
    <span class="header-phone">
      <svg width="10" height="10" viewBox="0 0 24 24"><path fill="#35c1b4" d="M6.6 10.8a15 15 0 006.6 6.6l2.2-2.2c.3-.3.7-.4 1-.2 1.1.4 2.3.6 3.6.6.6 0 1 .4 1 1V20c0 .6-.4 1-1 1A17 17 0 013 4c0-.6.4-1 1-1h3.5c.6 0 1 .4 1 1 0 1.3.2 2.5.6 3.6.1.3 0 .7-.2 1z"/></svg>
      310-555-0142
    </span>
  </div>
  <nav class="main-nav">
    <span>Home</span><span>Workstations</span><span>Components</span><span>Virtualization</span><span>Servers</span><span>About Us</span><span>Blog</span><span>Resources</span><span>Contact Us</span>
    <span class="search">Search</span><span class="cart-box"></span>
  </nav>
</header>

<div class="hero" role="img" aria-label="Office desk photo with laptop and plant"></div>

<h1 class="page-title">Contact Us</h1>

<section class="location">
  <div class="office-panel">
    <h3>Office Headquarters</h3>
    <p>Nexora Tech, LLC<br>1820 Alder Way<br>Westvale, CA 90000</p>
  </div>
  <div class="map" role="img" aria-label="Street map around the office"></div>
</section>

<section class="message-center">
  <h2>Message Center to Contact Us</h2>
  <div class="form">
    <div class="fields">
      <div class="field">Name</div>
      <div class="field">E-mail</div>
      <div class="field">Phone number</div>
    </div>
    <div class="message">Message</div>
  </div>
  <div class="submit">Submit</div>
</section>

<section class="info">
  <div class="hours">
    <h4>Hours of Operation</h4>
    <ul>
      <li>Monday: 8:00am - 5:00pm</li>
      <li>Tuesday: 8:00am - 5:00pm</li>
      <li>Wednesday: 8:00am - 5:00pm</li>
      <li>Thursday: 8:00am - 5:00pm</li>
      <li>Friday: 8:00am - 5:00pm</li>
    </ul>
    <p class="note">Our dedicated customer service representatives are available 24/7 by phone.</p>
    <h4 class="social-title">Stay Connected</h4>
    <div class="social"><span></span><span></span><span></span><span></span></div>
  </div>
  <div class="contact-info">
    <h4>Contact Info</h4>
    <div class="contact-grid">
      <div>
        <h5>General Inquiries</h5>
        <p><svg width="8" height="8" viewBox="0 0 24 24"><path fill="#35c1b4" d="M6.6 10.8a15 15 0 006.6 6.6l2.2-2.2c.3-.3.7-.4 1-.2 1.1.4 2.3.6 3.6.6.6 0 1 .4 1 1V20c0 .6-.4 1-1 1A17 17 0 013 4c0-.6.4-1 1-1h3.5c.6 0 1 .4 1 1 0 1.3.2 2.5.6 3.6.1.3 0 .7-.2 1z"/></svg>310-555-0142</p>
        <p><svg width="8" height="8" viewBox="0 0 24 24"><path fill="#35c1b4" d="M2 5h20v14H2zm2 2v1l8 5 8-5V7z"/></svg>info@nexoratech.com</p>
      </div>
      <div>
        <h5>Sales Inquiries</h5>
        <p><svg width="8" height="8" viewBox="0 0 24 24"><path fill="#35c1b4" d="M6.6 10.8a15 15 0 006.6 6.6l2.2-2.2c.3-.3.7-.4 1-.2 1.1.4 2.3.6 3.6.6.6 0 1 .4 1 1V20c0 .6-.4 1-1 1A17 17 0 013 4c0-.6.4-1 1-1h3.5c.6 0 1 .4 1 1 0 1.3.2 2.5.6 3.6.1.3 0 .7-.2 1z"/></svg>310-555-0142</p>
        <p><svg width="8" height="8" viewBox="0 0 24 24"><path fill="#35c1b4" d="M2 5h20v14H2zm2 2v1l8 5 8-5V7z"/></svg>sales@nexoratech.com</p>
      </div>
      <div>
        <h5>Purchasing Inquiries</h5>
        <p><svg width="8" height="8" viewBox="0 0 24 24"><path fill="#35c1b4" d="M6.6 10.8a15 15 0 006.6 6.6l2.2-2.2c.3-.3.7-.4 1-.2 1.1.4 2.3.6 3.6.6.6 0 1 .4 1 1V20c0 .6-.4 1-1 1A17 17 0 013 4c0-.6.4-1 1-1h3.5c.6 0 1 .4 1 1 0 1.3.2 2.5.6 3.6.1.3 0 .7-.2 1z"/></svg>310-555-0142</p>
        <p><svg width="8" height="8" viewBox="0 0 24 24"><path fill="#35c1b4" d="M2 5h20v14H2zm2 2v1l8 5 8-5V7z"/></svg>buy@nexoratech.com</p>
      </div>
    </div>
  </div>
</section>

<footer class="site-footer">
  <p class="footer-about">Nexora Tech, LLC builds custom workstations, servers, storage and virtualization systems for business and creative teams. Every system is assembled and tested in house by our engineers and backed by responsive support. We ship across the country and around the world, with friendly help available whenever you need it.</p>
  <div class="footer-contact">
    <span><svg width="8" height="8" viewBox="0 0 24 24"><path fill="#555" d="M12 2a7 7 0 00-7 7c0 5 7 13 7 13s7-8 7-13a7 7 0 00-7-7zm0 9.5A2.5 2.5 0 1112 6.5a2.5 2.5 0 010 5z"/></svg>1820 Alder Way<br>Westvale, CA 90000</span>
    <span><svg width="8" height="8" viewBox="0 0 24 24"><path fill="#555" d="M6.6 10.8a15 15 0 006.6 6.6l2.2-2.2c.3-.3.7-.4 1-.2 1.1.4 2.3.6 3.6.6.6 0 1 .4 1 1V20c0 .6-.4 1-1 1A17 17 0 013 4c0-.6.4-1 1-1h3.5c.6 0 1 .4 1 1 0 1.3.2 2.5.6 3.6.1.3 0 .7-.2 1z"/></svg>310-555-0142</span>
    <span><svg width="8" height="8" viewBox="0 0 24 24"><path fill="#555" d="M2 5h20v14H2zm2 2v1l8 5 8-5V7z"/></svg>sales@nexoratech.com</span>
  </div>
  <div class="footer-links">
    <span>Computer Hardware</span><span>Careers</span><span>Privacy Policy</span><span>About Us</span><span>Customer Support</span>
  </div>
  <div class="footer-bottom">
    <div class="footer-social"><span></span><span></span><span></span><span></span></div>
    <p class="copyright">Nexora Tech, LLC<br>Copyright ©<br>2015</p>
  </div>
</footer>
</body>
</html>
```